Plenko - Shoe Fitting App : Foot scanning app, 3D reconstruction and Fit recommandation.

We are a startup that has developed a 3D scanning App that compares the 3d reconstructed foot to the 3D Last (mould) of a shoe to find the best match and recommend a shoe size with a graphical representation of the fit on a reconstructed foot without texturing. The challenge of this app is to have a simple and intuitive onboarding of the user with clean and crisp ui and a simple tutorial for foot scanning. 3D representation of the fit is also key. What you see is what you feel is what we would like to achieve.

Target Market(s)

Sneaker Brands and athletic shoes brands

Industry/Entity Type

Footwear

Font styles to use
Other font styles liked:
• Oswald or Droid Serif

Colors
0094D4
00A9DD
6FCCEA
C7EBF8
E9F6FB

Requirements
Must have
• Simple intuitive UI to onboard the customer to scan his bare foot (please look at attached image on how to scan the foot). You must flip your phone so that the screen is facing your foot. Start at 40cm distance form the front of your foot and turn 360% slowly to capture the foot while you feel the aptic of the iPhone. That needs to be presented with a simple animation that the user can easily understand and skip if he is a returning customer and knows how to do that. the rest of the UI is to present the result of the scanned foot for the user to use to get his fit and size. The other must have is the final result screen. Where the user will a representation of the foot (snug, loose ) of different predefined areas of the foot so he can choose the fit that he likes and not necessarily the size that we suggest. Must match website design (https://www.plenko.example)
Nice to have
• An animation of the whole process (scan-compare 3d foot with 3d shoe last(or mould) and get the 3D result of the best fit + associated size. Optionaly, an option to play with your foot and transform it (avatar like with accessories and colours)
Should not have
• Too many colours. Too much text. No gender type. No race type.

```html
<!DOCTYPE html>
<html lang="en">
<head>
<meta charset="utf-8">
<title>Plenko – Foot Scanning Flow</title>
<link rel="stylesheet" href="https://fonts.googleapis.com/css2?family=Oswald:wght@500;600&family=Roboto:wght@400;500;700&display=swap">
<style>
  :root{
    --teal:#4bb3b3;
    --black:#000000;
    --white:#ffffff;
    --ink-dim:#1d3e3e;
    --page:#ffffff;
  }
  *{box-sizing:border-box;margin:0;padding:0}
  html,body{width:1200px;height:541px;overflow:hidden;background:var(--page)}
  body{font-family:"Roboto",Arial,sans-serif;color:var(--white)}
  .flow{position:relative;width:1200px;height:541px}
  .screen{position:absolute;top:39px;width:214px;height:464px;border-radius:11px;overflow:hidden;background:var(--black)}
  .screen .backdrop{position:absolute;inset:0;width:100%;height:100%}
  .screen > *:not(.backdrop){position:absolute}
  .wordmark{top:19px;left:0;width:100%;text-align:center;font-family:"Oswald",Arial,sans-serif;font-weight:600;font-size:27px;letter-spacing:1px;line-height:32px;color:var(--white)}
  .rule{top:63px;left:23px;width:168px;height:1px;background:rgba(255,255,255,.35)}
  .headline{top:75px;left:8px;width:198px;text-align:center;font-family:"Oswald",Arial,sans-serif;font-weight:500;font-size:13px;line-height:20.3px;text-transform:uppercase;color:var(--white)}
  .caption{top:341px;left:14px;width:186px;text-align:center;font-size:8.3px;line-height:15px}
  .pager{top:404px;left:0;width:100%;display:flex;justify-content:center;gap:3px}
  .pager span{width:5px;height:5px;border-radius:50%;background:var(--ink-dim)}
  .pager span.on{background:var(--teal)}
  .btn{display:flex;align-items:center;justify-content:center;height:26px;border-radius:13px;background:var(--teal);color:var(--white);font-size:8px;font-weight:500;letter-spacing:.2px;text-transform:uppercase}
  .btn.primary{top:424px;left:42px;width:131px}
  .btn.ghost{background:var(--white);color:var(--teal)}
  .visual{border-radius:4px}
  /* screen 1 */
  .s1 .visual{top:120px;left:0;width:214px;height:215px;border-radius:0;background:linear-gradient(180deg,#2a2a2a 0%,#1a1a1a 55%,#333230 75%,#060606 100%)}
  /* screen 2 */
  .s2 .visual{top:176px;left:20px;width:174px;height:142px;background:linear-gradient(180deg,#1d3a4c 0%,#3f7fa6 35%,#8a6a52 70%,#0c0c0c 100%)}
  /* screen 3 */
  .s3 .visual{top:154px;left:0;width:214px;height:310px;border-radius:0;background:linear-gradient(180deg,#3a3a3a 0%,#262626 55%,#151515 100%)}
  /* screen 4 */
  .s4 .caption{top:126px}
  .s4 .visual{top:187px;left:62px;width:90px;height:202px;border-radius:40px 40px 38px 38px;background:linear-gradient(180deg,#d9a77d 0%,#c98f66 55%,#a8704c 100%)}
  .eye{top:189px;left:171px;width:26px;height:26px;border-radius:50%;background:var(--teal);display:flex;align-items:center;justify-content:center}
  .s4 .btn.scan{top:424px;left:18px;width:84px}
  .s4 .btn.fit{top:424px;left:112px;width:84px}
  /* screen 5 */
  .progress{top:105px;left:31px;width:151px;height:2px;background:var(--white);border-radius:1px}
  .progress-label{top:110px;left:140px;width:42px;text-align:right;font-size:4.5px;font-weight:700}
  .facts-title{top:161px;left:0;width:100%;text-align:center;font-family:"Oswald",Arial,sans-serif;font-weight:500;font-size:12.5px;line-height:16px;text-transform:uppercase}
  .facts-text{top:182px;left:14px;width:186px;text-align:center;font-size:7.8px;line-height:15px;color:var(--white)}
  .pref-bar{top:222px;left:16px;width:183px;height:26px;background:var(--teal);display:flex;align-items:center;justify-content:center;font-family:"Oswald",Arial,sans-serif;font-weight:500;font-size:11px;text-transform:uppercase}
  .pref-question{top:256px;left:0;width:100%;text-align:center;font-size:7.8px}
  .panel{left:15px;width:184px;border:1px solid #1e1e1e;border-radius:5px}
  .panel.options{top:275px;height:82px}
  .panel.results{top:369px;height:81px}
  .pill{position:absolute;top:8px;width:45px;height:16px;border-radius:8px;display:flex;align-items:center;justify-content:center;font-size:5.5px;background:var(--white);color:var(--teal)}
  .pill.soft{left:20px}.pill.medium{left:68px;background:var(--teal);color:var(--white)}.pill.hard{left:117px}
  .options-text{position:absolute;top:32px;left:6px;width:172px;text-align:center;font-size:7.6px;line-height:14px}
  .options-nav{position:absolute;top:63px;left:0;width:100%;display:flex;justify-content:center}
  .results-text{position:absolute;top:7px;left:8px;width:168px;text-align:center;font-size:6.5px;line-height:12px}
  .btn.results-btn{position:absolute;top:51px;left:40px;width:104px;height:20px;border-radius:10px;font-size:6.2px}
</style>
</head>
<body>
<main class="flow">

  <!-- Step 1: lighting -->
  <section class="screen s1" style="left:19px">
    <div class="visual" role="img" aria-label="Spotlight shining down onto the floor of a dark room"></div>
    <svg class="backdrop" viewBox="0 0 214 464" preserveAspectRatio="none" aria-hidden="true"><path d="M0 0H214V158Q107 98 0 158Z" fill="var(--teal)"/></svg>
    <div class="wordmark">PLENKO</div>
    <div class="rule"></div>
    <h2 class="headline">Make sure you're in a<br>well lit area</h2>
    <p class="caption">Avoid strong light from only one direction.<br>This casts deep shadows that reduce<br>accuracy of the scan.</p>
    <div class="pager"><span class="on"></span><span></span><span></span></div>
    <div class="btn primary">Next</div>
  </section>

  <!-- Step 2: bare feet -->
  <section class="screen s2" style="left:256px">
    <svg class="backdrop" viewBox="0 0 214 464" preserveAspectRatio="none" aria-hidden="true"><path d="M0 0H214V158Q107 98 0 158Z" fill="var(--teal)"/></svg>
    <div class="wordmark">PLENKO</div>
    <div class="rule"></div>
    <h2 class="headline">Take off your shoes &amp;<br>roll up pants</h2>
    <div class="visual" role="img" aria-label="Legs in rolled-up jeans with bare feet, socks and sneakers set aside"></div>
    <p class="caption">To scan your feet, the camera needs<br>to see the unique details, including Your<br>ankle</p>
    <div class="pager"><span></span><span class="on"></span><span></span></div>
    <div class="btn primary">Next</div>
  </section>

  <!-- Step 3: scanning -->
  <section class="screen s3" style="left:493px">
    <div class="visual" role="img" aria-label="Dotted point-cloud outline of a foot being scanned"></div>
    <svg class="backdrop" viewBox="0 0 214 464" preserveAspectRatio="none" aria-hidden="true"><path d="M0 0H214V184Q107 124 0 184Z" fill="var(--teal)"/></svg>
    <div class="wordmark">PLENKO</div>
    <div class="rule"></div>
    <h2 class="headline">Flip the screen<br>towards your toes to<br>start scanning</h2>
    <div class="btn primary">Right foot</div>
  </section>

  <!-- Step 4: reconstruction check -->
  <section class="screen s4" style="left:730px">
    <svg class="backdrop" viewBox="0 0 214 464" preserveAspectRatio="none" aria-hidden="true"><path d="M0 0H214V117Q107 59 0 117Z" fill="var(--teal)"/></svg>
    <div class="wordmark">PLENKO</div>
    <div class="rule"></div>
    <p class="caption">Please check that the reconstruction of your<br>foot seems correct.</p>
    <div class="visual" role="img" aria-label="3D reconstruction of a bare foot seen from below"></div>
    <div class="eye"><svg width="12" height="8" viewBox="0 0 12 8" aria-hidden="true"><path d="M0.5 4Q6 -2 11.5 4Q6 10 0.5 4Z" fill="var(--white)"/><circle cx="6" cy="4" r="1.8" fill="var(--teal)"/></svg></div>
    <div class="btn scan">Scan again</div>
    <div class="btn ghost fit">My fit</div>
  </section>

  <!-- Step 5: results -->
  <section class="screen s5" style="left:967px">
    <svg class="backdrop" viewBox="0 0 214 464" preserveAspectRatio="none" aria-hidden="true"><path d="M0 0H214V158Q107 98 0 158Z" fill="var(--teal)"/></svg>
    <div class="wordmark">PLENKO</div>
    <div class="rule"></div>
    <h2 class="headline">You're all measured up</h2>
    <div class="progress"></div>
    <div class="progress-label">100%</div>
    <h3 class="facts-title">Fun facts about feet</h3>
    <p class="facts-text">Our feet have nearly a qauarte of all the<br>bones-each one has 26 bones.</p>
    <div class="pref-bar">Tell us your preference</div>
    <p class="pref-question">How do you prefer the cushion?</p>
    <div class="panel options">
      <span class="pill soft">Soft</span>
      <span class="pill medium">Medium</span>
      <span class="pill hard">Hard</span>
      <p class="options-text">Select an option to go the next personal<br>preference setting.</p>
      <div class="options-nav"><svg width="16" height="8" viewBox="0 0 16 8" aria-hidden="true"><path d="M5 1L2 4L5 7M11 1L14 4L11 7" stroke="var(--white)" stroke-width="1.4" fill="none"/></svg></div>
    </div>
    <div class="panel results">
      <p class="results-text">Click below to see how this shoe fits. Now that<br>you're scanned, you can quickly try other shoes<br>without going through the process again.</p>
      <div class="btn results-btn">See results</div>
    </div>
  </section>

</main>
</body>
</html>
```